Banner ads for LP that work with same theme as below banners

Love the banner ads below. Need more with attached photos. But use the same wording, font as in below banner ads. Should be LP size 1200/627 so I can use for Pixorly and LP. Looking for great ads to use as LP ads. We do lots of ads so it will be worth your time to enter this contest you will be rewarded with a ton of work. Need several banner ads that work together. So maybe 1 of the dresses, 1 of the sweater, 1 of the leggings, 1 of the jacket

Target Market(s)

Women 24-45

Industry/Entity Type

Fashion

Requirements
Must have
• Banner ads that work for LP and Pixorly
Nice to have
• Several options to choose from
Should not have
• not sure

```html
<!DOCTYPE html>
<html lang="en">
<head>
<meta charset="utf-8">
<title>Our Best Sweater Ever</title>
<link rel="stylesheet" href="https://fonts.googleapis.com/css2?family=Dancing+Script:wght@500&family=Playfair+Display:wght@400;700&display=swap">
<style>
  :root {
    --sky-top: #e7ece3;
    --sky-haze: #d3dbd8;
    --cloud-blue: #8fa3b0;
    --horizon: #c9d3d8;
    --peak-blue: #7b909f;
    --valley-dark: #4e6373;
    --snow-base: #a9b8c3;
    --studio-grey: #e5e5e8;
    --studio-edge: #d6d6da;
    --knit-grey: #b9b9bc;
    --knit-lilac: #c9c7d8;
    --band-light: rgba(228, 234, 240, 0.42);
    --accent-pink: #d2136c;
    --ink: #2b2b2b;
    --ghost: rgba(110, 110, 110, 0.13);
    --button-bg: #1b1b1b;
    --button-text: #ffffff;
  }
  * { margin: 0; padding: 0; box-sizing: border-box; }
  html, body { width: 1200px; height: 627px; overflow: hidden; background: #ffffff; }
  .banner {
    position: relative;
    width: 1200px;
    height: 627px;
    overflow: hidden;
  }
  .scenery {
    position: absolute;
    inset: 0;
    background:
      radial-gradient(ellipse 60% 22% at 70% 20%, rgba(90, 115, 135, 0.45), transparent 70%),
      radial-gradient(ellipse 50% 18% at 20% 30%, rgba(120, 140, 150, 0.3), transparent 70%),
      linear-gradient(180deg,
        var(--sky-top) 0%,
        var(--sky-haze) 22%,
        var(--cloud-blue) 42%,
        var(--horizon) 60%,
        var(--peak-blue) 74%,
        var(--valley-dark) 88%,
        var(--snow-base) 100%);
  }
  .photo {
    position: absolute;
    top: 0;
    width: 304px;
    height: 627px;
  }
  .photo--left {
    left: 76px;
    background: linear-gradient(90deg, var(--studio-edge), var(--studio-grey) 20%, var(--studio-grey) 80%, var(--studio-edge));
  }
  .photo--right {
    left: 820px;
    background: var(--band-light);
  }
  .photo__model {
    position: absolute;
    bottom: 0;
    border-radius: 120px 120px 0 0;
  }
  .photo--left .photo__model {
    left: 24px;
    width: 260px;
    height: 592px;
    background: linear-gradient(180deg, #c9b08a 0%, var(--knit-grey) 28%, var(--knit-grey) 92%, #2a2a2a 100%);
  }
  .photo--right .photo__model {
    left: 22px;
    width: 272px;
    height: 577px;
    background: linear-gradient(180deg, #8f7458 0%, var(--knit-lilac) 30%, var(--knit-lilac) 96%, #2a2a2a 100%);
  }
  .ghost-word {
    position: absolute;
    left: 380px;
    top: 218px;
    width: 480px;
    text-align: center;
    font-family: "Playfair Display", Georgia, serif;
    font-weight: 400;
    font-size: 90px;
    letter-spacing: 10px;
    line-height: 1;
    color: var(--ghost);
    white-space: nowrap;
  }
  .headline {
    position: absolute;
    left: 400px;
    width: 400px;
    top: 185px;
    text-align: center;
  }
  .headline__script {
    display: block;
    font-family: "Dancing Script", cursive;
    font-weight: 500;
    font-size: 46px;
    letter-spacing: 6px;
    color: var(--accent-pink);
    line-height: 1.2;
  }
  .headline__product {
    display: block;
    font-family: "Playfair Display", Georgia, serif;
    font-weight: 700;
    font-size: 44px;
    letter-spacing: 6px;
    color: var(--ink);
    line-height: 1.15;
  }
  .cta {
    position: absolute;
    left: 519px;
    top: 377px;
    width: 163px;
    height: 43px;
    background: var(--button-bg);
    color: var(--button-text);
    font-family: "Playfair Display", Georgia, serif;
    font-size: 12px;
    letter-spacing: 2px;
    display: flex;
    align-items: center;
    justify-content: center;
    gap: 6px;
    text-decoration: none;
  }
  .cta__strong { font-weight: 700; }
  .cta__light { font-weight: 400; }
</style>
</head>
<body>
  <main class="banner">
    <div class="scenery" role="img" aria-label="Snowy mountain range under a cloudy sky"></div>

    <div class="photo photo--left">
      <div class="photo__model" role="img" aria-label="Model wearing an oversized grey knit turtleneck sweater"></div>
    </div>
    <div class="photo photo--right">
      <div class="photo__model" role="img" aria-label="Model wearing an oversized lilac knit turtleneck sweater"></div>
    </div>

    <span class="ghost-word" aria-hidden="true">SWEATER</span>

    <h1 class="headline">
      <span class="headline__script">Our Best</span>
      <span class="headline__product">SWEATER</span>
      <span class="headline__script">Ever!</span>
    </h1>

    <a class="cta" href="#"><span class="cta__strong">SHOP</span><span class="cta__light">THE</span><span class="cta__strong">LOOK</span></a>
  </main>
</body>
</html>
```